Casa Morellina Togo Menu seperated in categories

new to go menu for italian restaurant with menu descriptions and prices i like the cover first page to have all the restaurant information, the other pages should be separated in the menu categories, and if we can include a map with the location of the restaurant
Casa Morellina
42 Route 83 S
North Myrtle Beach, SC 29582
open 7 days a week 4-10
Happy hour served Daily at the Bar 4-7
www.casamorellina.com
casamorellinadine@maildrop.example

Restaurant

Sans Serif

Must have
• Prices and pictures and restaurant information

```html
<!DOCTYPE html>
<html lang="en">
<head>
<meta charset="utf-8">
<title>Casa Morellina – To Go Menu</title>
<link href="https://fonts.googleapis.com/css2?family=Oswald:wght@400;500;600&family=Open+Sans:wght@400&display=swap" rel="stylesheet">
<style>
  :root{
    --paper:#ffffff;
    --ink:#111111;
    --text:#2a2a2a;
    --accent:#a3242f;
  }
  html,body{margin:0;padding:0;overflow:hidden;background:var(--paper);}
  .menu-page{
    position:relative;width:667px;height:1200px;background:var(--paper);overflow:hidden;
    font-family:"Open Sans",Arial,sans-serif;color:var(--text);
  }
  .menu-frame{
    position:absolute;left:40px;top:39px;width:585px;height:1120px;
    border:2px solid var(--accent);
  }
  .section-title{
    position:absolute;left:70px;margin:0;
    font-family:"Oswald",Impact,sans-serif;font-weight:500;
    font-size:60px;line-height:1;letter-spacing:-0.3px;color:var(--ink);
    transform:scaleY(1.17);transform-origin:left top;
  }
  .addons{
    position:absolute;left:299px;top:770px;
    font-size:14px;line-height:26px;color:var(--ink);
  }
  .addons span{font-family:"Oswald",sans-serif;font-weight:500;font-size:18px;color:var(--accent);margin-left:4px;}
  .menu-item{position:absolute;left:71px;width:518px;}
  .item-head{display:flex;align-items:baseline;height:24px;}
  .item-name{
    font-family:"Oswald",Impact,sans-serif;font-weight:500;font-size:18.5px;color:var(--ink);
    white-space:nowrap;
  }
  .item-leader{
    flex:1;margin:0 8px;border-bottom:1.5px dashed var(--accent);transform:translateY(-6px);
  }
  .item-price{
    font-family:"Oswald",Impact,sans-serif;font-weight:400;font-size:19px;color:var(--accent);
    width:34px;text-align:right;
  }
  .item-desc{margin:2px 0 0;font-size:13.8px;line-height:17.5px;color:var(--text);width:522px;}
</style>
</head>
<body>
<main class="menu-page">
  <div class="menu-frame"></div>

  <h2 class="section-title" style="top:95px;">ANTIPASTI</h2>

  <div class="menu-item" style="top:185px;">
    <div class="item-head"><span class="item-name">Mozzarella Completa</span><span class="item-leader"></span><span class="item-price">9.95</span></div>
    <p class="item-desc">Mozzarella, Roasted Red Peppers, Ricotta Cheese, Fresh Tomatoes, Prosciutto Di Parma, Drizzled with Evoo &amp; Aged Balsamic</p>
  </div>
  <div class="menu-item" style="top:267px;">
    <div class="item-head"><span class="item-name">Fried Calamari</span><span class="item-leader"></span><span class="item-price">8.95</span></div>
    <p class="item-desc">Calamari Lightly Breaded, Fried to Perfection, Served with Homemade Spicy Marinara Sauce</p>
  </div>
  <div class="menu-item" style="top:349px;">
    <div class="item-head"><span class="item-name">Escargot</span><span class="item-leader"></span><span class="item-price">9.95</span></div>
    <p class="item-desc">Escargot in a Creamy Gorgonzola Cheese Sauce, Garlic, Sundried Tomatoes, Baked to Perfection</p>
  </div>
  <div class="menu-item" style="top:432px;">
    <div class="item-head"><span class="item-name">Zuppa Di Cozze</span><span class="item-leader"></span><span class="item-price">8.95</span></div>
    <p class="item-desc">Fresh PEI Mussels in a choice of Marinara or Lemon Fusion Sauce</p>
  </div>
  <div class="menu-item" style="top:495px;">
    <div class="item-head"><span class="item-name">Mozzarella Caprese</span><span class="item-leader"></span><span class="item-price">8.95</span></div>
    <p class="item-desc">Fresh Tomato, Homemade Mozzarella, Fresh Basil, Roasted Red Peppers, Evoo and Balsamic</p>
  </div>
  <div class="menu-item" style="top:580px;">
    <div class="item-head"><span class="item-name">Shrimp Florentine</span><span class="item-leader"></span><span class="item-price">11.95</span></div>
    <p class="item-desc">Jumbo Shrimp wrapped in Prosciutto, in a Lemon Infusion Sauce, served over Spinach</p>
  </div>
  <div class="menu-item" style="top:662px;">
    <div class="item-head"><span class="item-name">Clams Oreganata</span><span class="item-leader"></span><span class="item-price">8.95</span></div>
    <p class="item-desc">Fresh Little Neck Clams topped with Italian Seasoned Bred Crumbs and Baked to Perfection</p>
  </div>

  <h2 class="section-title" style="top:754px;">INSALATA</h2>
  <div class="addons">
    <div>Add Chicken <span>3.95</span></div>
    <div>Add Shrimp <span>5.95</span></div>
  </div>

  <div class="menu-item" style="top:841px;">
    <div class="item-head"><span class="item-name">Italian Salad</span><span class="item-leader"></span><span class="item-price">8.95</span></div>
    <p class="item-desc">Fresh Mixed Greens, Tomatoes, Cucumbers, Onions, Mozzarella, Banana Peppers, tossed in our homemade Italian Dressing</p>
  </div>
  <div class="menu-item" style="top:920px;">
    <div class="item-head"><span class="item-name">Insalata Gorgonzola</span><span class="item-leader"></span><span class="item-price">9.95</span></div>
    <p class="item-desc">Fresh Romaine Lettuce, Gorgonzola, thin sliced Pear, Red Onions, Walnuts, in our homemade Italian Dressing</p>
  </div>
  <div class="menu-item" style="top:1002px;">
    <div class="item-head"><span class="item-name">Greek Salad</span><span class="item-leader"></span><span class="item-price">8.95</span></div>
    <p class="item-desc">Mixed Greens, Tomatoes, Cucumbers, Red Onions, Bell Peppers, Kalamata Olives and Feta Cheese in our homemade Italian Dressing</p>
  </div>
  <div class="menu-item" style="top:1085px;">
    <div class="item-head"><span class="item-name">Caesar Salad</span><span class="item-leader"></span><span class="item-price">7.95</span></div>
    <p class="item-desc">Fresh Romaine Tossed with Caesar Dressing, Croutons, topped with Parmesan Cheese</p>
  </div>
</main>
</body>
</html>
```